New stationary design for online film company

We need some new stationary to fit with our new logo. The stationary should be professional, clean and simple.
We need designs for a full set of business stationary.
We need - letterhead, envelopes, invoices, proposals, coverslip/note and cover page

Industry/Entity Type

Business

```html
<!DOCTYPE html>
<html lang="en">
<head>
<meta charset="utf-8">
<title>Lumenreel Stationery Set</title>
<link href="https://fonts.googleapis.com/css2?family=Open+Sans:wght@400;600;700&display=swap" rel="stylesheet">
<style>
  :root {
    --navy: #0d4a73;
    --sky: #6ea6c2;
    --brand: #3f7fa6;
    --ink: #2b3440;
    --muted: #8aa9bf;
    --paper: #ffffff;
    --ground: #e8e6e3;
    --ghost: #e6ecf2;
  }
  * { box-sizing: border-box; margin: 0; padding: 0; }
  html, body { width: 1200px; height: 778px; overflow: hidden; }
  body {
    background: var(--ground);
    font-family: "Open Sans", Arial, sans-serif;
    color: var(--ink);
    position: relative;
  }
  .brand-name {
    font-family: "Open Sans", Arial, sans-serif;
    font-weight: 600;
    color: var(--brand);
    letter-spacing: -0.5px;
    line-height: 1;
  }
  .wave { position: absolute; left: 0; bottom: 0; width: 100%; display: block; }

  /* Letterhead */
  .letterhead {
    position: absolute; left: 14px; top: 18px; width: 525px; height: 740px;
    background: var(--paper);
    box-shadow: 0 2px 6px rgba(0,0,0,.18);
    overflow: hidden;
  }
  .letterhead .brand-name { position: absolute; left: 30px; top: 42px; font-size: 30px; }
  .contact-list {
    position: absolute; left: 408px; top: 26px;
    border-left: 1px solid #c9d3dc; padding-left: 8px;
    list-style: none; font-size: 9.5px; line-height: 14.5px; color: var(--ink);
  }
  .contact-list li { display: flex; align-items: center; gap: 5px; }
  .contact-list svg { width: 8px; height: 8px; flex: none; }
  .letterhead .ghost-mark {
    position: absolute; left: 170px; top: 250px; width: 210px; height: 210px;
    border-radius: 50%; border: 26px solid var(--ghost);
  }
  .letterhead .wave { height: 60px; }
  .letterhead .footer-address {
    position: absolute; left: 38px; bottom: 17px;
    color: #fff; font-size: 9px; line-height: 13px;
  }

  /* Business cards */
  .card {
    position: absolute; top: 22px; width: 222px; height: 126px;
    background: var(--paper);
    box-shadow: 0 2px 5px rgba(0,0,0,.18);
    overflow: hidden;
  }
  .card-front { left: 579px; }
  .card-front .brand-name {
    position: absolute; left: 0; right: 0; top: 48px; text-align: center; font-size: 24px;
  }
  .card-front .card-web {
    position: absolute; left: 0; right: 0; bottom: 8px; text-align: center;
    font-size: 5.5px; letter-spacing: 1.3px; font-weight: 600; color: var(--ink);
  }
  .card-back { left: 814px; }
  .card-back .brand-name { position: absolute; left: 20px; top: 55px; font-size: 15px; }
  .card-back .divider {
    position: absolute; left: 122px; top: 18px; width: 1px; height: 70px; background: #d3dbe2;
  }
  .card-back .person { position: absolute; left: 131px; top: 22px; }
  .person-name { font-size: 8px; font-weight: 700; color: var(--navy); }
  .person-role { font-size: 6px; color: var(--muted); margin-top: 1px; }
  .card-back .contact-mini {
    position: absolute; left: 131px; top: 48px; list-style: none;
    font-size: 5.5px; line-height: 10px; color: var(--ink);
  }
  .contact-mini li { display: flex; align-items: center; gap: 3px; }
  .contact-mini svg { width: 5px; height: 5px; flex: none; }
  .card-back .wave { height: 30px; }
  .card-back .card-address {
    position: absolute; left: 15px; bottom: 4px; color: #fff; font-size: 5px; line-height: 7px;
  }

  /* Envelopes */
  .envelope-stack { position: absolute; left: 569px; top: 169px; width: 614px; height: 580px; }
  .envelope-backs { position: absolute; left: 0; top: 0; }
  .flap-label { font-family: "Open Sans", Arial, sans-serif; font-weight: 600; font-size: 18px; }
  .envelope-front {
    position: absolute; left: 10px; top: 309px; width: 603px; height: 270px;
    background: var(--paper);
    border: 1px solid #c8c8c8;
    box-shadow: 0 2px 6px rgba(0,0,0,.15);
    overflow: hidden;
  }
  .envelope-front .brand-name { position: absolute; left: 27px; top: 38px; font-size: 28px; }
  .envelope-front .return-address {
    position: absolute; left: 27px; top: 79px; font-size: 9px; letter-spacing: 0.8px; color: var(--ink);
  }
  .envelope-front .ghost-mark {
    position: absolute; right: 30px; top: 185px; width: 56px; height: 56px;
    border-radius: 50%; border: 7px solid var(--ghost);
  }
  .envelope-front .wave { height: 60px; }
  .envelope-front .envelope-web {
    position: absolute; left: 33px; bottom: 21px; color: #fff;
    font-size: 8px; font-weight: 600; letter-spacing: 2px;
  }
</style>
</head>
<body>

<svg width="0" height="0" style="position:absolute" aria-hidden="true">
  <defs>
    <symbol id="icon-phone" viewBox="0 0 10 10">
      <circle cx="5" cy="5" r="4.4" fill="none" stroke="#2b3440" stroke-width="0.9"/>
      <path d="M3.4 3 L4.3 3 L4.6 4.1 L4 4.5 Q4.6 5.6 5.6 6 L6 5.4 L7 5.7 L7 6.6 Q4 7 3.4 3 Z" fill="#2b3440"/>
    </symbol>
    <symbol id="icon-mobile" viewBox="0 0 10 10">
      <rect x="3" y="1" width="4.4" height="8" rx="0.8" fill="#2b3440"/>
      <rect x="3.8" y="2" width="2.8" height="5" fill="#fff"/>
    </symbol>
    <symbol id="icon-mail" viewBox="0 0 10 10">
      <rect x="0.8" y="2.3" width="8.4" height="5.6" fill="#2b3440"/>
      <path d="M1 2.6 L5 5.6 L9 2.6" fill="none" stroke="#fff" stroke-width="0.8"/>
    </symbol>
    <symbol id="icon-web" viewBox="0 0 10 10">
      <circle cx="5" cy="5" r="4.2" fill="none" stroke="#2b3440" stroke-width="0.9"/>
      <ellipse cx="5" cy="5" rx="1.8" ry="4.2" fill="none" stroke="#2b3440" stroke-width="0.7"/>
      <path d="M0.8 5 H9.2 M1.6 2.8 H8.4 M1.6 7.2 H8.4" stroke="#2b3440" stroke-width="0.6"/>
    </symbol>
    <symbol id="wave-band" viewBox="0 0 600 60" preserveAspectRatio="none">
      <path d="M0 8 Q180 -4 330 16 T600 22" fill="none" stroke="#0d4a73" stroke-width="2"/>
      <path d="M0 13 Q190 2 340 22 T600 28" fill="none" stroke="#6ea6c2" stroke-width="1.2"/>
      <path d="M0 18 Q200 8 350 28 T600 34" fill="none" stroke="#6ea6c2" stroke-width="1"/>
      <path d="M0 20 Q210 12 360 32 T600 38 V60 H0 Z" fill="#0d4a73"/>
    </symbol>
  </defs>
</svg>

<!-- Letterhead -->
<section class="letterhead" aria-label="Letterhead">
  <div class="brand-name">lumenreel</div>
  <ul class="contact-list">
    <li><svg><use href="#icon-phone"/></svg>123-456-7890</li>
    <li><svg><use href="#icon-mail"/></svg>info@lumenreel.com</li>
    <li><svg><use href="#icon-web"/></svg>www.lumenreel.com</li>
  </ul>
  <div class="ghost-mark" aria-hidden="true"></div>
  <svg class="wave" aria-hidden="true" preserveAspectRatio="none"><use href="#wave-band"/></svg>
  <p class="footer-address">00, Complex Name<br>street, city 000452</p>
</section>

<!-- Business card front -->
<section class="card card-front" aria-label="Business card front">
  <div class="brand-name">lumenreel</div>
  <p class="card-web">www.lumenreel.com</p>
</section>

<!-- Business card back -->
<section class="card card-back" aria-label="Business card back">
  <div class="brand-name">lumenreel</div>
  <div class="divider"></div>
  <div class="person">
    <p class="person-name">Your Name</p>
    <p class="person-role">Designation</p>
  </div>
  <ul class="contact-mini">
    <li><svg><use href="#icon-phone"/></svg>123-456-7890</li>
    <li><svg><use href="#icon-mobile"/></svg>123-456-7890</li>
    <li><svg><use href="#icon-mail"/></svg>info@lumenreel.com</li>
    <li><svg><use href="#icon-web"/></svg>www.lumenreel.com</li>
  </ul>
  <svg class="wave" aria-hidden="true" preserveAspectRatio="none"><use href="#wave-band"/></svg>
  <p class="card-address">00, Complex Name<br>street, city 000452</p>
</section>

<!-- Envelopes -->
<section class="envelope-stack" aria-label="Envelopes">
  <svg class="envelope-backs" width="614" height="480" viewBox="0 0 614 480" aria-hidden="true">
    <rect x="13" y="0" width="600" height="300" fill="#ffffff"/>
    <path d="M13 0 H613 L603 30 Q598 48 575 52 L313 82 L51 52 Q28 48 23 30 Z" fill="#6ea6c2"/>
    <text class="flap-label" x="313" y="48" text-anchor="middle" fill="#ffffff">lumenreel</text>

    <rect x="13" y="81" width="600" height="320" fill="#ffffff"/>
    <path d="M13 81 H613 L603 115 Q598 135 575 138 L335 185 Q313 189 291 185 L51 138 Q28 135 23 115 Z" fill="#0d4a73"/>
    <text class="flap-label" x="313" y="138" text-anchor="middle" fill="#ffffff">lumenreel</text>

    <rect x="0.5" y="197" width="602" height="272" fill="#ffffff" stroke="#c8c8c8" stroke-width="0.8"/>
    <path d="M0.5 197 H602.5 L597 220 Q592 245 565 250 L320 297 Q301 300 282 297 L40 250 Q12 245 7 220 Z" fill="#ffffff" stroke="#333" stroke-width="0.8"/>
    <text class="flap-label" x="301" y="258" text-anchor="middle" fill="#3f7fa6">lumenreel</text>
  </svg>

  <div class="envelope-front">
    <div class="brand-name">lumenreel</div>
    <p class="return-address">00, Complex Name, street, city 000452</p>
    <div class="ghost-mark" aria-hidden="true"></div>
    <svg class="wave" aria-hidden="true" preserveAspectRatio="none"><use href="#wave-band"/></svg>
    <p class="envelope-web">www.lumenreel.com</p>
  </div>
</section>

</body>
</html>
```